Specialized Personal Trainer Needs a Business Card Design

I need a business card design for my personal training business called Tall Oak Fitness. I have my Human Kinetics degree in Exercise Science from the Halvering Polytechnic Institute as well as an extra certification from NFBP (National Federation of Body Practice). I work as a Cardiac Rehab Exercise Specialist and personal trainer giving specialized exercise prescriptions to those that have different heart conditions as well as work with the general population in weight loss, strength and conditioning, getting/staying fit.
Updates

I decided that I wanted a logo (as I did not have one before I submitted my project for a business card) so I am submitting a project to get a logo done and then I will decide on a business card, hopefully being able to use one of the designs already submitted.  My apologies for doing this backwards.  I am new to this so I appreciate your patience.

Thank you.

Hi, I have just created a project for a logo design (I realized I needed a logo and I should've done that first..oops!), please feel free to participate.  Once I receive a logo I like I will finalize my business card project and hopefully incorporate it into one of your business card designs. 

Thank you!

Target Market(s)

Business professionals

Industry/Entity Type

Personal Trainer

Requirements
Must have
• My name with my info:
Delphine R. Ashcroft (BHK)
NFBP Certified Clinical Exercise Specialist & Personal Trainer
del.ashcroft@talloakfitness.example
Cell: 555-302-6148

Please make it double sided.
Nice to have
• An image that represents cardiac and general fitness training.

```html
<!DOCTYPE html>
<html lang="en">
<head>
<meta charset="utf-8">
<title>Tall Oak Fitness – Business Card</title>
<link rel="stylesheet" href="https://fonts.googleapis.com/css2?family=Jost:wght@400;500&display=swap">
<style>
  :root {
    --page-bg: #e9e6e1;
    --card-black: #050505;
    --accent-yellow: #d4dc1c;
    --text-light: #e8e8e8;
    --text-dark: #111111;
    --figure-blue: #3b63c8;
    --figure-glow: #14244f;
  }
  * { box-sizing: border-box; margin: 0; padding: 0; }
  html, body {
    width: 1200px; height: 880px; overflow: hidden;
    background: var(--page-bg);
    font-family: "Jost", "Futura", sans-serif;
  }
  .sheet {
    position: relative; width: 1200px; height: 880px;
  }
  .card {
    position: absolute; left: 280px;
    width: 640px; height: 366px;
    background: var(--card-black);
    overflow: hidden;
    box-shadow: 0 6px 18px rgba(0,0,0,0.25);
  }
  .card--front { top: 50px; }
  .card--back { top: 464px; }

  /* Front */
  .identity {
    position: absolute; left: 30px; top: 150px;
    display: flex; align-items: center;
  }
  .identity__name {
    color: var(--text-light);
    font-size: 22px; font-weight: 400;
    letter-spacing: 1px; text-transform: uppercase;
    white-space: nowrap;
  }
  .identity__divider {
    width: 2px; height: 40px;
    background: var(--accent-yellow);
    margin: 0 12px 0 14px;
  }
  .identity__title {
    color: var(--text-light);
    font-size: 11px; line-height: 1.4;
  }
  .contact {
    position: absolute; left: 18px; top: 255px;
    width: 410px; padding: 9px 14px;
    background: var(--accent-yellow);
    color: var(--text-dark);
    font-size: 17px; line-height: 1.3;
  }

  /* Back */
  .body-visual {
    position: absolute; inset: 0;
    background:
      radial-gradient(ellipse 32% 22% at 48% 45%, rgba(230,80,110,0.55), transparent 70%),
      radial-gradient(ellipse 55% 38% at 50% 50%, var(--figure-blue), var(--figure-glow) 55%, var(--card-black) 85%);
  }
  .brand-strip {
    position: absolute; right: 0; bottom: 0;
    width: 56px; height: 220px;
    background: var(--accent-yellow);
    display: flex; align-items: center; justify-content: center;
  }
  .brand-strip__name {
    transform: rotate(-90deg);
    white-space: nowrap;
    color: var(--text-dark);
    font-size: 24px; font-weight: 400;
  }
</style>
</head>
<body>
<main class="sheet">
  <section class="card card--front">
    <div class="identity">
      <h1 class="identity__name">Delphine R. Ashcroft (BHK)</h1>
      <span class="identity__divider"></span>
      <p class="identity__title">NFBP Certified Clinical Exercise<br>Specialist &amp; Personal Trainer</p>
    </div>
    <div class="contact">
      <p>del.ashcroft@talloakfitness.example</p>
      <p>Cell: 555-302-6148</p>
    </div>
  </section>

  <section class="card card--back">
    <div class="body-visual" role="img" aria-label="Glowing blue anatomical human figure in motion with a highlighted red heart and circulatory system"></div>
    <div class="brand-strip">
      <span class="brand-strip__name">Tall Oak Fitness</span>
    </div>
  </section>
</main>
</body>
</html>
```